Financial Advisor Resource Firm needs business card design

Need business card design for company in Omaha NE called Meridale Circle. We provide resources to financial advisors....workshop programs, retirement analysis, and insurance planning. I would like to see designs that use grays, greens, black, and white colors. The final design should communicate 'collaboration' and be simple yet attractive to financial planning clients. I will attached our logo and another picture of a puzzle piece coming together. I would like the incorporate the puzzle picture somehow, maybe on the back somehow, with color or just the gray scale....OR, the picture be the front of the card with 'Meridale' definition on it (see upload) and then company logo, employee name, title, address on the back (see ppt uploaded). The following disclosure needs to be included somewhere- Advisory services offered through Stonebrook Assets, LLC.
Updates

I uploaded a svg and ai file of the logo

Target Market(s)

Financial planning clients and financial advisors....so pretty diverse age range of about 40-70.

Industry/Entity Type

Financial Planning

Contact Information for Business Card

Tobias L. Fenwright, MBA
Founder/President
5287 E. Larkin Road
Suite 230
Omaha, NE 68190
Phone- (402) 555-0147
Cell- (402) 555-0183
Fax- (402) 555-0129
email- tobias@meridaleplan.example
web address- www.meridaleplan.example

Colors
1b1b1b
474747
d3d3d3
ffffff
9bcb3c
abd036

Requirements
Must have
• Must include logo provided, must be 2 sided, and must have disclosure...all of these items listed in project description

```html
<!DOCTYPE html>
<html lang="en">
<head>
<meta charset="utf-8">
<title>Meridale Circle – Business Card</title>
<link rel="stylesheet" href="https://fonts.googleapis.com/css2?family=Source+Sans+3:wght@400;600;700&display=swap">
<style>
  :root {
    --ink: #1b1b1b;
    --graphite: #474747;
    --silver: #d3d3d3;
    --white: #ffffff;
    --leaf: #9bcb3c;
    --lime: #abd036;
    --backdrop: #e9e9e7;
  }
  * { box-sizing: border-box; margin: 0; padding: 0; }
  html, body { width: 1200px; height: 900px; overflow: hidden; }
  body {
    background: var(--backdrop);
    font-family: "Source Sans 3", "Helvetica Neue", Arial, sans-serif;
    color: var(--white);
    position: relative;
  }
  .card {
    position: absolute;
    width: 560px;
    height: 320px;
    border-radius: 12px;
    overflow: hidden;
    background: var(--graphite);
    box-shadow: 0 10px 28px rgba(0,0,0,.22);
  }
  .card-front { left: 70px; top: 90px; }
  .card-back { left: 570px; top: 480px; }

  .photo-fill {
    position: absolute; inset: 0;
    background:
      radial-gradient(ellipse at 70% 55%, rgba(140,140,140,.45), transparent 60%),
      linear-gradient(135deg, #2a2a2a 0%, var(--graphite) 55%, #262626 100%);
  }
  .card-back .photo-fill {
    background:
      radial-gradient(ellipse at 78% 50%, rgba(150,150,150,.4), transparent 55%),
      linear-gradient(120deg, #2b2b2b 0%, #3a3a3a 50%, #2e2e2e 100%);
  }

  .wordmark {
    display: flex; align-items: center; gap: 12px;
    font-weight: 600;
    color: var(--white);
    letter-spacing: .04em;
    text-transform: uppercase;
    white-space: nowrap;
  }
  .wordmark-dot {
    width: 22px; height: 22px; border-radius: 50%;
    border: 3px solid var(--white);
    flex: none;
  }

  .front-content {
    position: absolute; inset: 0;
    display: flex; flex-direction: column; align-items: center;
  }
  .front-content .wordmark { font-size: 40px; margin-top: 104px; }
  .tagline {
    margin-top: 70px;
    font-size: 14.5px;
    letter-spacing: .06em;
    text-transform: uppercase;
    color: var(--white);
  }

  .back-content { position: absolute; inset: 0; padding: 26px 34px 0; }
  .back-content .wordmark { font-size: 36px; margin-left: 28px; }
  .holder-name {
    margin-top: 20px;
    font-size: 24px; font-weight: 700; line-height: 1.1;
    color: var(--leaf);
  }
  .holder-title { font-size: 16px; margin-top: 3px; line-height: 1.2; }
  .contact-row {
    display: flex; gap: 22px; margin-top: 10px;
    font-size: 16px; line-height: 1.2;
  }
  .contact-row.split { justify-content: space-between; margin-top: 8px; }
  .contact-item { display: flex; align-items: center; gap: 7px; white-space: nowrap; }
  .contact-item svg { width: 13px; height: 13px; fill: var(--leaf); flex: none; }
  .rule {
    height: 1px; margin-top: 8px;
    background: linear-gradient(90deg, rgba(171,208,54,.8), rgba(211,211,211,.5));
  }
  .address { font-size: 16px; margin-top: 7px; line-height: 1.2; }
  .disclosure {
    font-size: 11px; margin-top: 8px; line-height: 1.2;
    color: var(--silver);
    letter-spacing: .02em;
  }
</style>
</head>
<body>

  <section class="card card-front" aria-label="Card front">
    <div class="photo-fill" role="img" aria-label="Grayscale photo of hands joining puzzle pieces"></div>
    <div class="front-content">
      <div class="wordmark"><span class="wordmark-dot"></span>Meridale Circle</div>
      <p class="tagline">To come together and unite in common interest and focus</p>
    </div>
  </section>

  <section class="card card-back" aria-label="Card back">
    <div class="photo-fill" role="img" aria-label="Grayscale photo of hands fitting puzzle pieces together"></div>
    <div class="back-content">
      <div class="wordmark"><span class="wordmark-dot"></span>Meridale Circle</div>
      <h1 class="holder-name">Tobias L. Fenwright, MBA</h1>
      <p class="holder-title">Founder/President</p>

      <div class="contact-row">
        <span class="contact-item">
          <svg viewBox="0 0 16 16" aria-hidden="true"><path d="M3.6 1.2l2.3 2.6-1.4 1.9c.9 2 2.6 3.7 4.6 4.6l1.9-1.4 2.6 2.3-1.4 2.6C6.8 13.9 2.1 9.2 1 3.8z"/></svg>
          (402) 555-0147
        </span>
        <span class="contact-item">
          <svg viewBox="0 0 16 16" aria-hidden="true"><path d="M4.5 0h7a1 1 0 011 1v14a1 1 0 01-1 1h-7a1 1 0 01-1-1V1a1 1 0 011-1zm1 2v10h5V2zm2.5 11a1 1 0 100 2 1 1 0 000-2z"/></svg>
          (402) 555-0183
        </span>
        <span class="contact-item">
          <svg viewBox="0 0 16 16" aria-hidden="true"><path d="M4 0h6l2 2v4h2a2 2 0 012 2v6H0V8a2 2 0 012-2h2zm1 1v5h6V2.5L9.5 1zM3 10v3h10v-3z"/></svg>
          (402) 555-0129
        </span>
      </div>

      <div class="contact-row split">
        <span class="contact-item">
          <svg viewBox="0 0 16 16" aria-hidden="true"><path d="M0 3h16v10H0zm1.5 1.2L8 9l6.5-4.8V4h-13z"/></svg>
          tobias@meridaleplan.example
        </span>
        <span class="contact-item">
          <svg viewBox="0 0 16 16" aria-hidden="true"><path d="M8 0a8 8 0 100 16A8 8 0 008 0zm0 1.5c.9 0 1.9 1.6 2.3 4H5.7C6.1 3.1 7.1 1.5 8 1.5zM5.6 7h4.8a12 12 0 010 2H5.6a12 12 0 010-2zm-4 0h2.5a14 14 0 000 2H1.6a6.5 6.5 0 010-2zm10.3 0h2.5a6.5 6.5 0 010 2h-2.5a14 14 0 000-2zM5.7 10.5h4.6c-.4 2.4-1.4 4-2.3 4s-1.9-1.6-2.3-4z"/></svg>
          www.meridaleplan.example
        </span>
      </div>

      <div class="rule"></div>
      <p class="address">5287 E. Larkin Road Suite 230 Omaha, NE 68190</p>
      <p class="disclosure">Advisory services offered through Stonebrook Assets, LLC.</p>
    </div>
  </section>

</body>
</html>
```